Need a landing page design updated

Need an existing landing page perfected, want it too look similar to one of Quorbel's landing pages in that it flows and is really aesthetically pleasing. The link to the landing page is below. I need this design updated asap. Please take the content directly from the page.

http://verdantmoxfl.com/residential-services/

Target Market(s)

High end residential landscape customers on the gulf coast of Florida (Clearwater area)

Industry/Entity Type

Landscape Gardening

Font styles to use
Sans Serif
Decorative

Requirements
Must have
• I want to keep the written content the same on on the landing page, but would like to work on making both aesthetically appealing to the consumer. This is for high end residential clients on the gulf coast of florida, so think palm trees and sunny beaches with beautiful houses and gorgeous landscapes....look through www.verdantmoxfl.com home page for an example of the houses we landscape.
Nice to have
• Would like it to flow as you scroll similar to Quorbel's landing pages.
• Look at how Quorbel's landing page flows, want similar here.....
• https://www.quorbel.com/zentaphone-v/
Should not have
• this landing page must be beautiful and must make a lot of sense as you scroll, am looking for a work of art....please do not submit generic templates or anything that can be easily done....I need real artistry.

```html
<!DOCTYPE html>
<html lang="en">
<head>
<meta charset="utf-8">
<title>Verdantmox – Residential Landscaping</title>
<link href="https://fonts.googleapis.com/css2?family=Lato:wght@400;700;900&display=swap" rel="stylesheet">
<style>
:root{
  --blue:#1b9ed6;
  --blue-dark:#1485b8;
  --ink:#2b2b2b;
  --text:#444;
  --grey:#f1f1f1;
  --white:#fff;
  --black:#1c1c1c;
  --leaf:#5f8a3a;
  --leaf-dark:#3e5e25;
  --sky:#9cc8e6;
}
*{box-sizing:border-box;margin:0;padding:0}
html,body{width:1200px;height:5172px;overflow:hidden}
body{font-family:'Lato',sans-serif;color:var(--text);background:var(--white);position:relative}
section,header,footer{position:relative;width:1200px;overflow:hidden}
.photo{position:absolute}
.h-blue{color:var(--blue);font-weight:900;text-transform:uppercase}

/* header */
.site-header{height:105px;background:var(--white)}
.brand{position:absolute;left:76px;top:30px;display:flex;align-items:center;gap:10px;font-size:28px;font-weight:700;color:var(--blue);letter-spacing:1px;text-transform:uppercase}
.brand-dot{width:14px;height:14px;border-radius:50%;background:var(--blue)}
.topbar{position:absolute;right:62px;top:16px;display:flex;align-items:center;gap:12px;font-size:13px;font-weight:700;color:var(--ink)}
.topbar .phone{color:var(--blue);font-size:16px}
.btn-dark{background:var(--black);color:var(--white);padding:9px 14px;font-size:12px;font-weight:700}
.btn-blue{background:var(--blue);color:var(--white);padding:9px 14px;font-size:12px;font-weight:700}
.main-nav{position:absolute;right:62px;top:70px;display:flex;gap:30px;font-size:13px;font-weight:700;color:var(--ink)}
.main-nav .active{color:var(--blue)}

/* hero */
.hero{height:600px}
.hero .photo{inset:0;background:linear-gradient(180deg,var(--sky) 0%,#cfe2ef 35%,#e8dcc3 55%,var(--leaf) 80%,var(--leaf-dark) 100%)}
.hero svg{position:absolute;left:0;bottom:0}

/* split rows */
.split{display:block}
.split .copy{position:absolute}
.copy p{font-size:22px;line-height:1.45}
.copy h3{font-size:19px;margin-bottom:18px}
.ticks{list-style:none}
.ticks li{position:relative;padding-left:34px;font-size:16px;line-height:1.45;margin-bottom:16px;color:var(--text)}
.ticks li svg{position:absolute;left:0;top:3px}

.guess{height:330px}
.guess .photo{left:76px;top:40px;width:528px;height:230px;background:linear-gradient(180deg,#8ec3e8 0%,#a9cfe8 40%,#d9c8a8 65%,#7f9a5c 100%)}
.guess .copy{left:636px;top:70px;width:470px}
.guess h2{font-size:36px;color:var(--blue);font-weight:900;margin-bottom:8px}
.guess p{font-size:22px;color:var(--text)}

.sunset{height:570px}
.sunset .band{position:absolute;inset:0}
.sunset .photo{left:604px;top:90px;width:596px;height:400px;background:linear-gradient(180deg,#3b5d2c 0%,#6e9a40 45%,#8ec04c 100%)}
.sunset .copy{left:76px;top:200px;width:480px;color:var(--white)}
.sunset .copy p{margin-bottom:14px}

.dreams{height:180px;text-align:center;padding-top:40px}
.dreams h2{font-size:26px;color:var(--blue);font-weight:900;text-transform:uppercase;line-height:1.3;width:800px;margin:0 auto}
.dreams p{font-size:24px;color:var(--text);margin-top:4px;line-height:1.3}

.generic{height:400px}
.generic .photo{left:0;top:30px;width:604px;height:370px;background:linear-gradient(135deg,#3f6a2c 0%,#b19b86 45%,#9b8670 60%,#547a35 100%)}
.generic .copy{left:640px;top:110px;width:470px}

.tailor{height:420px}
.tailor .photo{left:604px;top:0;width:596px;height:400px;background:linear-gradient(180deg,#2f78c4 0%,#6aa7dc 40%,#6f9e3e 65%,#4d7f28 100%)}
.tailor .copy{left:76px;top:80px;width:490px}

.experts{height:450px;background:var(--blue)}
.experts .photo{left:0;top:0;width:604px;height:450px;background:linear-gradient(180deg,#3c5e2a 0%,#6d9740 55%,#7fb04a 100%)}
.experts .copy{left:644px;top:90px;width:500px;color:var(--white)}
.experts h3{font-size:23px;font-weight:400;line-height:1.35;margin-bottom:18px;text-transform:none}
.experts p{font-size:17px;line-height:1.5}

.benefits{height:420px;background:var(--grey);text-align:center;padding-top:60px}
.benefits h2{font-size:24px;color:var(--ink);font-weight:900;text-transform:uppercase}
.benefit-grid{display:flex;justify-content:center;gap:60px;margin-top:40px}
.benefit{width:300px}
.benefit .icon{width:96px;height:96px;border-radius:50%;background:var(--blue);margin:0 auto 26px;display:flex;align-items:center;justify-content:center}
.benefit p{font-size:17px;line-height:1.45;color:var(--text)}

.worry{height:380px}
.worry .photo{left:0;top:0;width:604px;height:380px;background:linear-gradient(135deg,#2f5f24 0%,#5f8d35 50%,#8aa84a 100%)}
.worry .copy{left:644px;top:110px;width:480px}
.worry h3{font-size:18px;line-height:1.4;margin-bottom:14px}
.worry p{font-size:18px;line-height:1.45}

.flaws{height:370px}
.flaws .photo{left:604px;top:0;width:596px;height:370px;background:linear-gradient(180deg,#7db4e6 0%,#b9d6ec 40%,#8b7058 60%,#5d8a3a 100%)}
.flaws .copy{left:76px;top:120px;width:480px}
.flaws h3{font-size:18px;line-height:1.4;margin-bottom:16px}

.clients{height:375px;background:var(--grey);text-align:center;padding-top:70px}
.clients h2{font-size:26px;color:var(--blue);font-weight:900;text-transform:uppercase;width:900px;margin:0 auto;line-height:1.3}
.clients .lead{font-size:24px;color:var(--text);margin:6px 0 28px}
.clients blockquote{font-size:16px;line-height:1.5;color:var(--ink);width:880px;margin:0 auto 18px}

.cta{height:420px}
.cta .band{position:absolute;inset:0}
.lead-form{position:absolute;left:172px;top:120px;width:440px}
.lead-form .field{height:52px;background:var(--white);border:1px solid #ddd;display:flex;align-items:center;justify-content:center;font-size:14px;color:#555;margin-bottom:10px}
.lead-form .submit{height:52px;background:var(--black);color:var(--white);display:flex;align-items:center;justify-content:center;font-size:15px;font-weight:700;letter-spacing:1px}
.cta .copy{position:absolute;left:644px;top:120px;width:480px;color:var(--white)}
.cta .copy p{font-size:25px;line-height:1.35}
.cta .copy p+p{margin-top:20px}

.site-footer{height:152px;text-align:center;padding-top:30px}
.site-footer small{font-size:12px;color:#666}
.social{display:flex;justify-content:center;gap:18px;margin-top:16px}
.social span{width:22px;height:22px;border-radius:50%;background:#555}
</style>
</head>
<body>

<header class="site-header">
  <div class="brand"><span class="brand-dot"></span>Verdantmox</div>
  <div class="topbar">
    <span>CALL US NOW ON : <span class="phone">727-555-0148</span></span>
    <span class="btn-dark">CLIENT PORTAL</span>
    <span class="btn-blue">GET A FREE QUOTE</span>
  </div>
  <nav class="main-nav">
    <span class="active">HOME</span><span>ABOUT US</span><span>RESIDENTIAL</span><span>COMMERCIAL</span><span>BLOG</span><span>CONTACT US</span>
  </nav>
</header>

<section class="hero">
  <div class="photo" role="img" aria-label="Florida villa with palm trees and a green front lawn"></div>
  <svg width="1200" height="120" viewBox="0 0 1200 120" preserveAspectRatio="none">
    <path d="M0 70 C300 10 600 120 900 60 C1020 36 1120 40 1200 60 L1200 120 L0 120 Z" fill="var(--blue)" opacity=".85"/>
    <path d="M0 90 C320 40 620 130 900 80 C1040 56 1130 64 1200 80 L1200 120 L0 120 Z" fill="var(--white)"/>
  </svg>
</section>

<section class="split guess">
  <div class="photo" role="img" aria-label="Palm-lined driveway leading to a luxury home"></div>
  <div class="copy">
    <h2>LET'S GUESS:</h2>
    <p>You don't have an abundance of free time. And, you simply don't want to spend the little time you have – mowing a lawn and pruning the plants.</p>
  </div>
</section>

<section class="split sunset">
  <svg class="band" width="1200" height="570" viewBox="0 0 1200 570" preserveAspectRatio="none">
    <path d="M0 70 C260 0 520 40 760 80 C960 112 1100 70 1200 40 L1200 520 C900 580 500 500 0 540 Z" fill="var(--blue)"/>
  </svg>
  <div class="photo" role="img" aria-label="Garden patio with wooden table and a kettle grill on the lawn"></div>
  <div class="copy">
    <p>You would probably like to spend that time the way you should, instead.</p>
    <p>Enjoying the sunset in the privacy of your garden, watching a favorite TV show while lying on a hammock, or throwing an occasional BBQ party with your friends and loved ones.</p>
  </div>
</section>

<section class="dreams">
  <h2>Getting an outdoor area of your dreams is not that difficult, nor expensive.</h2>
  <p>You can make this happen by getting a help from a landscaping company<br>that offers tailor-made services.</p>
</section>

<section class="split generic">
  <div class="photo" role="img" aria-label="Curving paved garden path between green shrubs"></div>
  <div class="copy">
    <h3 class="h-blue">Generic landscaping services:</h3>
    <ul class="ticks">
      <li><svg width="18" height="18" viewBox="0 0 18 18"><path d="M2 9l5 5 9-10" stroke="var(--blue)" stroke-width="2.5" fill="none"/></svg>You pay for the bundle of services, regardless of whether you actually need them.</li>
      <li><svg width="18" height="18" viewBox="0 0 18 18"><path d="M2 9l5 5 9-10" stroke="var(--blue)" stroke-width="2.5" fill="none"/></svg>You get a generic service, not adjusted to the specific needs of your outdoor area.</li>
      <li><svg width="18" height="18" viewBox="0 0 18 18"><path d="M2 9l5 5 9-10" stroke="var(--blue)" stroke-width="2.5" fill="none"/></svg>The field team thinks of your property as just another task they have to complete.</li>
    </ul>
  </div>
</section>

<section class="split tailor">
  <div class="photo" role="img" aria-label="Gardener mowing a wide lawn under a blue sky"></div>
  <div class="copy">
    <h3 class="h-blue">Tailor-made landscaping services:</h3>
    <ul class="ticks">
      <li><svg width="18" height="18" viewBox="0 0 18 18"><path d="M2 9l5 5 9-10" stroke="var(--blue)" stroke-width="2.5" fill="none"/></svg>You pay only for the services your yard really needs.</li>
      <li><svg width="18" height="18" viewBox="0 0 18 18"><path d="M2 9l5 5 9-10" stroke="var(--blue)" stroke-width="2.5" fill="none"/></svg>You get your garden's specific issues solved, and specific requirements met.</li>
      <li><svg width="18" height="18" viewBox="0 0 18 18"><path d="M2 9l5 5 9-10" stroke="var(--blue)" stroke-width="2.5" fill="none"/></svg>The field team members take their time working on your property.</li>
      <li><svg width="18" height="18" viewBox="0 0 18 18"><path d="M2 9l5 5 9-10" stroke="var(--blue)" stroke-width="2.5" fill="none"/></svg>They get to learn all about your vision – and make it a reality.</li>
    </ul>
  </div>
</section>

<section class="split experts">
  <div class="photo" role="img" aria-label="Landscaper pushing a lawn mower across a garden"></div>
  <div class="copy">
    <h3>Why should you care that Verdantmox employs the leading industry experts and uses modern, eco-friendly technical solutions?</h3>
    <p>That is why we're able to transform your lawn into a green carpet and get your plants in a perfect health. All while keeping your vision and your budget on our minds. That is why our services actually enable you to reduce the operating expenses.</p>
  </div>
</section>

<section class="benefits">
  <h2>More benefits of having a well-maintained yard:</h2>
  <div class="benefit-grid">
    <div class="benefit">
      <div class="icon"><svg width="48" height="44" viewBox="0 0 48 44"><rect x="4" y="28" width="8" height="14" fill="#fff"/><rect x="18" y="20" width="8" height="22" fill="#fff"/><rect x="32" y="12" width="8" height="30" fill="#fff"/><path d="M4 20 L20 8 L30 14 L44 2" stroke="#fff" stroke-width="3" fill="none"/></svg></div>
      <p>In some cases, a great-looking lawn can increase your property's value up to 20%.</p>
    </div>
    <div class="benefit">
      <div class="icon"><svg width="44" height="44" viewBox="0 0 44 44"><circle cx="22" cy="22" r="18" stroke="#fff" stroke-width="3" fill="none"/><circle cx="22" cy="22" r="8" fill="#fff"/></svg></div>
      <p>Your lawn and plants reduce the energy consumption – countering the warming effects of paved surfaces.</p>
    </div>
    <div class="benefit">
      <div class="icon"><svg width="48" height="40" viewBox="0 0 48 40"><rect x="4" y="6" width="24" height="28" stroke="#fff" stroke-width="3" fill="none"/><path d="M22 20 H44 M36 12 L44 20 L36 28" stroke="#fff" stroke-width="3" fill="none"/></svg></div>
      <p>They act as giant dust filters, increasing air quality, and removing carbon dioxide from the atmosphere.</p>
    </div>
  </div>
</section>

<section class="split worry">
  <div class="photo" role="img" aria-label="Gardener trimming a hedge with shears"></div>
  <div class="copy">
    <h3 class="h-blue">Do you worry our services are going to disturb you while trying to unwind in the privacy of your own garden?</h3>
    <p>Our Client Service Operators Build A Schedule Around Your Needs –Designed Not To Disturb You At All.</p>
  </div>
</section>

<section class="split flaws">
  <div class="photo" role="img" aria-label="Backyard lawn with wooden fence and trees"></div>
  <div class="copy">
    <h3 class="h-blue">Do our services have flaws?<br>Yes. They have two giant ones.</h3>
    <ul class="ticks">
      <li><svg width="18" height="18" viewBox="0 0 18 18"><path d="M2 9l5 5 9-10" stroke="var(--blue)" stroke-width="2.5" fill="none"/></svg>Your "new" garden will get all of your neighbors jealous</li>
      <li><svg width="18" height="18" viewBox="0 0 18 18"><path d="M2 9l5 5 9-10" stroke="var(--blue)" stroke-width="2.5" fill="none"/></svg>Your friends will probably start inviting themselves over more frequently.</li>
    </ul>
  </div>
</section>

<section class="clients">
  <h2>At Verdantmox, we do more than just keeping your landscape in a pristine state.</h2>
  <p class="lead">This is what some of our long-term clients say about our approach:</p>
  <blockquote>"We are delighted with your landscaping, both with the design and implementation.It's not very often these days that work exceeds expectations."</blockquote>
  <blockquote>"Verdantmox are efficient, on-time, responsive, provide fair pricing, do outstanding work, have great people, and actually follow up on their work."</blockquote>
</section>

<section class="cta">
  <svg class="band" width="1200" height="420" viewBox="0 0 1200 420" preserveAspectRatio="none">
    <path d="M0 40 C300 90 600 0 900 30 C1040 44 1130 60 1200 50 L1200 380 C900 420 400 350 0 390 Z" fill="var(--blue)"/>
  </svg>
  <form class="lead-form">
    <div class="field">Name</div>
    <div class="field">Phone or Email Address</div>
    <div class="submit">GET STARTED</div>
  </form>
  <div class="copy">
    <p>So, what's the next step to enriching your living area?<br>And getting you a garden from your dreams.</p>
    <p>It's simple, just book a no-obligations consultation..</p>
  </div>
</section>

<footer class="site-footer">
  <small>Copyright © 2017 Verdantmox All Rights Reserved</small>
  <div class="social"><span></span><span></span><span></span><span></span><span></span></div>
</footer>

</body>
</html>
```